Marcus Delbridge Finance

Need a personal website advertising Equipment Finance,Business Finance,Commercial Finance, Construction Finance, Bridging Finance. Similar websites are www.corvalend.com.au / www.tarmivest.com.au / www.qbr7.com.au /wwwhalvecredit.com.au

Target Market(s)

Business People

Industry/Entity Type

Business

Number of Pages Required

3 page

Font styles to use
Serif
Sans Serif

Requirements
Must have
• All i want is a simple corporate looking website advertising Equipment Finance, Commercial Finance, Construction Finance, Business Finance, Bridging Finance,

```html
<!DOCTYPE html>
<html lang="en">
<head>
<meta charset="utf-8">
<title>Marcus Delbridge Finance</title>
<link rel="stylesheet" href="https://fonts.googleapis.com/css2?family=Tinos:ital,wght@0,400;0,700;1,400&family=Open+Sans:ital,wght@0,400;0,600;1,400&family=Raleway:wght@400;500&display=swap">
<style>
:root{
  --navy:#1b4a85;
  --navy-dark:#153b6b;
  --band:#1e4d86;
  --footer:#0c5297;
  --accent:#1f6fba;
  --ink:#222;
  --muted:#555;
  --grey-strip:#e4e4e4;
  --copy-bar:#383838;
  --white:#fff;
  --serif:'Tinos', 'Times New Roman', serif;
  --sans:'Open Sans', Arial, sans-serif;
  --display:'Raleway', Arial, sans-serif;
}
*{box-sizing:border-box;margin:0;padding:0}
html,body{width:1200px;height:2594px;overflow:hidden;background:#fff}
body{position:relative;font-family:var(--sans);color:var(--ink)}
.abs{position:absolute}

/* header */
.top-strip{left:726px;top:0;width:474px;height:35px;background:var(--grey-strip);clip-path:polygon(20px 0,100% 0,100% 100%,0 100%)}
.call{left:756px;top:6px;display:flex;align-items:center;gap:8px;font-size:12px;color:#333}
.call .ico{width:22px;height:22px;border-radius:50%;background:var(--navy);display:flex;align-items:center;justify-content:center}
.socials{display:flex;gap:6px}
.socials span{width:28px;height:28px;border-radius:50%;background:var(--navy);display:block}
.top-socials{left:916px;top:4px}
.brand{left:171px;top:80px;display:flex;align-items:center;gap:10px;font-family:var(--serif);font-weight:700;font-size:20px;color:var(--navy);letter-spacing:.5px}
.brand i{width:14px;height:14px;background:var(--navy);display:block}
.search{left:788px;top:57px;width:250px;height:38px;display:flex}
.search .field{flex:1;border:1px solid #ccc;font-family:var(--serif);font-size:13px;color:#999;padding:10px 12px}
.search .btn{width:40px;background:var(--navy);display:flex;align-items:center;justify-content:center}
.nav{left:0;top:114px;width:1200px;height:45px;background:linear-gradient(#22568f,var(--navy-dark));border-top:2px solid #2c6aa8}
.nav ul{list-style:none;display:flex;gap:25px;position:absolute;left:175px;top:12px;font-family:var(--serif);font-size:15px;color:#fff}

/* hero */
.hero{left:0;top:159px;width:1200px;height:501px;background:linear-gradient(180deg,#8e9aa6 0%,#c9ced3 40%,#9aa3ab 70%,#59626b 100%)}
.hero-arrow{top:384px;width:22px;height:28px;background:#333;display:flex;align-items:center;justify-content:center}
.hero-caption{left:0;top:600px;width:1200px;height:60px;background:rgba(20,20,20,.72);color:#fff;font-family:var(--display);font-size:27px;text-align:center;line-height:60px}

/* about */
.about-title{left:0;top:690px;width:1200px;text-align:center;font-family:var(--serif);font-size:33px;color:var(--ink)}
.about-title span{color:var(--accent)}
.rule{left:540px;width:120px;height:1px;background:#bbb}
.rule::after{content:"";position:absolute;left:44px;top:-1px;width:32px;height:3px;background:var(--navy)}
.about-copy{left:170px;top:778px;width:860px;text-align:center;font-size:11px;line-height:18px;color:#333}

/* services hexes */
.hex{width:208px;height:238px;clip-path:polygon(50% 0,100% 25%,100% 75%,50% 100%,0 75%,0 25%);background:#d9d9d9}
.hex .inner{position:absolute;inset:9px;clip-path:polygon(50% 0,100% 25%,100% 75%,50% 100%,0 75%,0 25%)}
.hex .label{position:absolute;left:0;right:0;top:162px;text-align:center;font-family:var(--serif);font-size:17px;color:#fff;text-shadow:0 1px 2px rgba(0,0,0,.5)}
.hex.services .inner{background:var(--navy);display:flex;align-items:center;justify-content:center;text-align:center;font-family:var(--serif);font-size:38px;line-height:42px;color:#fff}

/* why choose */
.why{left:0;top:1407px;width:1200px;height:434px;background:var(--band);overflow:hidden}
.why-title{left:0;top:1448px;width:1200px;text-align:center;font-family:var(--serif);font-size:30px;color:#fff}
.why-item{color:#fff;width:260px}
.why-item h3{font-family:var(--serif);font-weight:700;font-size:16px;line-height:18px}
.why-item p{font-size:11.5px;line-height:17px;margin-top:4px}
.why-item.left{text-align:right}
.why-icon{width:68px;height:68px;border-radius:50%;background:#fff;display:flex;align-items:center;justify-content:center;box-shadow:0 0 0 3px rgba(255,255,255,.25)}
.why-hub{left:440px;top:1703px;width:320px;height:320px;border-radius:50%;background:#fff;border:5px solid #2f6fb3;display:flex;justify-content:center;padding-top:80px;font-family:var(--serif);font-weight:700;font-size:20px;color:var(--navy)}

/* testimonials */
.test-title{left:0;top:1905px;width:1200px;text-align:center;font-family:var(--serif);font-size:29px}
.test-title span{color:var(--accent)}
.quote{left:225px;top:1985px;width:750px;text-align:center;font-family:Arial,sans-serif;font-style:italic;font-size:14.5px;line-height:26px;color:#333}
.qmark{font-family:var(--serif);font-size:50px;color:#bbb;line-height:1}
.chev{top:2008px}
.client{left:0;top:2076px;width:1200px;text-align:center}
.client b{display:block;font-weight:600;color:var(--accent);font-size:15px}
.client small{display:block;font-size:13px;color:#333;margin-top:4px}
.dots{left:573px;top:2141px;display:flex;gap:6px}
.dots span{width:8px;height:8px;border-radius:50%;background:#aaa}
.dots span:first-child{background:var(--navy)}

/* newsletter */
.newsletter{left:0;top:2199px;width:1200px;height:66px;background:linear-gradient(#4a4a4a,#1f1f1f)}
.nl-title{left:258px;top:2216px;font-family:var(--serif);font-size:27px;color:#fff}
.nl-input{left:660px;top:2215px;width:258px;height:31px;background:#fff;font-size:11px;color:#555;padding:8px 10px}
.nl-btn{left:918px;top:2215px;width:121px;height:31px;background:var(--accent);color:#fff;font-size:13px;text-align:center;line-height:31px;letter-spacing:.5px}

/* footer */
.footer{left:0;top:2265px;width:1200px;height:282px;background:var(--footer)}
.col-title{top:2310px;font-family:var(--serif);font-size:18px;color:#fff}
.divider{top:2310px;width:1px;height:220px;background:rgba(255,255,255,.25)}
.links{left:164px;top:2352px;list-style:none;font-family:var(--serif);font-size:13px;line-height:22.5px;color:#fff}
.links li::before{content:"› ";}
.map{left:372px;top:2360px;width:200px;height:120px;background:radial-gradient(ellipse at center,rgba(255,255,255,.12),rgba(255,255,255,0) 70%)}
.contact{left:358px;top:2354px;font-family:var(--serif);font-size:13px;color:#fff}
.contact .row{display:flex;gap:8px;align-items:flex-start;margin-bottom:14px;line-height:19px}
.contact .dot{width:18px;height:18px;border-radius:50%;background:#fff;flex:none;display:flex;align-items:center;justify-content:center}
.inq{left:607px;width:209px;background:#fff;font-size:11px;color:#444;padding:7px 8px}
.submit{left:607px;top:2497px;width:104px;height:32px;background:#111;color:#fff;font-family:var(--serif);font-size:15px;line-height:32px;padding-left:12px}
.foot-social{left:857px;top:2352px}
.foot-social span{width:32px;height:32px;border-radius:50%;background:#fff}
.copyright{left:0;top:2547px;width:1200px;height:47px;background:var(--copy-bar);color:#ddd;font-family:var(--serif);font-size:13px;text-align:center;line-height:47px}
</style>
</head>
<body>

<header>
  <div class="abs top-strip"></div>
  <div class="abs call">
    <span class="ico"><svg width="12" height="12" viewBox="0 0 24 24"><path fill="#fff" d="M6.6 10.8a15 15 0 0 0 6.6 6.6l2.2-2.2a1 1 0 0 1 1-.25 11.4 11.4 0 0 0 3.6.57 1 1 0 0 1 1 1V20a1 1 0 0 1-1 1A17 17 0 0 1 3 4a1 1 0 0 1 1-1h3.5a1 1 0 0 1 1 1c0 1.25.2 2.45.57 3.57a1 1 0 0 1-.25 1z"/></svg></span>
    Call : 123-555-0147
  </div>
  <div class="abs socials top-socials"><span></span><span></span><span></span><span></span></div>
  <div class="abs brand"><i></i>MARCUS DELBRIDGE FINANCE</div>
  <div class="abs search">
    <div class="field">Search here...</div>
    <div class="btn"><svg width="18" height="18" viewBox="0 0 24 24" fill="none" stroke="#fff" stroke-width="3"><circle cx="10" cy="10" r="6.5"/><path d="M15 15l6 6"/></svg></div>
  </div>
  <nav class="abs nav">
    <ul>
      <li>Home</li><li>Equipment Finance</li><li>Business Finance</li><li>Commercial Finance</li><li>Construction Finance</li><li>Bridging Finance</li><li>Contact Us</li>
    </ul>
  </nav>
</header>

<section>
  <div class="abs hero" role="img" aria-label="Business people leaping across the gap of an unfinished bridge above a city skyline"></div>
  <div class="abs hero-arrow" style="left:4px"><svg width="8" height="12" viewBox="0 0 8 12"><path d="M6 1L1 6l5 5" stroke="#fff" stroke-width="2" fill="none"/></svg></div>
  <div class="abs hero-arrow" style="left:1164px;background:#fff"><svg width="8" height="12" viewBox="0 0 8 12"><path d="M2 1l5 5-5 5" stroke="#333" stroke-width="2" fill="none"/></svg></div>
  <div class="abs hero-caption">Focus on What you do Best, While We take care of your finances</div>
</section>

<section>
  <h1 class="abs about-title" style="font-weight:400">About Marcus Delbridge <span>- Finance</span></h1>
  <div class="abs rule" style="top:745px"></div>
  <p class="abs about-copy">Lorem ipsum dolor sit amet, consectetuer adipiscing elit, sed diam nonummy nibh euismod tincidunt ut laoreet dolore magna aliquam erat volutpat. Ut wisi enim ad minim veniam, quis nostrud exerci tation ullamcorper suscipit lobortis nisl ut aliquip ex ea commodo consequat. Duis autem vel eum iriure dolor in hendrerit in vulputate velit esse molestie consequat, vel illum dolore eu feugiat nulla facilisis at vero eros et accumsan et iusto odio dignissim qui blandit praesent. Ut wisi enim ad minim veniam, quis nostrud exerci tation. Luptatum zzril delenit augue duis dolore te feugait nulla facilisi.</p>

  <div class="abs hex" style="left:273px;top:921px"><div class="inner" role="img" aria-label="Excavator on a building site" style="background:linear-gradient(#5b6f8c,#3c3f3a)"></div><div class="label">Equipment Finance</div></div>
  <div class="abs hex services" style="left:498px;top:921px"><div class="inner">Our<br>Services</div></div>
  <div class="abs hex" style="left:722px;top:921px"><div class="inner" role="img" aria-label="Hands reviewing business charts on paper" style="background:linear-gradient(135deg,#9fb6cc,#4f6f93)"></div><div class="label">Business Finance</div></div>

  <div class="abs hex" style="left:159px;top:1120px"><div class="inner" role="img" aria-label="Business handshake in front of office towers" style="background:linear-gradient(#3e5a7c,#22334a)"></div><div class="label">Commercial Finance</div></div>
  <div class="abs hex" style="left:385px;top:1120px"><div class="inner" role="img" aria-label="High-rise tower under construction with cranes" style="background:linear-gradient(#8aa0b7,#4a3b30)"></div><div class="label">Construction Finance</div></div>
  <div class="abs hex" style="left:610px;top:1120px"><div class="inner" role="img" aria-label="Arch of balanced stones by the sea" style="background:linear-gradient(#8ea1b0,#7a6d58)"></div><div class="label">Bridging Finance</div></div>
  <div class="abs hex" style="left:831px;top:1120px"><div class="inner" role="img" aria-label="Hands signing a document at a desk" style="background:linear-gradient(#c8c6c2,#8b8680)"></div><div class="label">Others</div></div>
</section>

<section>
  <div class="abs why">
    <svg class="abs" style="left:0;top:0" width="1200" height="434">
      <circle cx="600" cy="478" r="204" fill="none" stroke="#fff" stroke-width="1.5" stroke-dasharray="2 4"/>
      <g fill="#1e4d86" stroke="#fff" stroke-width="2">
        <circle cx="446" cy="364" r="6"/><circle cx="484" cy="298" r="6"/><circle cx="558" cy="256" r="6"/>
        <circle cx="642" cy="256" r="6"/><circle cx="716" cy="298" r="6"/><circle cx="754" cy="364" r="6"/>
      </g>
      <g stroke="#fff" stroke-width="1" stroke-dasharray="2 3">
        <path d="M558 256L536 240M484 298L466 280M446 364L414 362M642 256L664 240M716 298L734 280M754 364L786 362"/>
      </g>
    </svg>
  </div>
  <h2 class="abs why-title" style="font-weight:400">Why Choose Us</h2>
  <div class="abs rule" style="top:1492px;background:rgba(255,255,255,.4)"></div>

  <div class="abs why-item left" style="left:219px;top:1530px"><h3>Unbiased Recommendations</h3><p>Lorem ipsum dolor sit mork<br>[+]...adipiscing sed diam</p></div>
  <div class="abs why-item left" style="left:114px;top:1614px"><h3>Unparalleled<br>Service</h3><p>Lorem ipsum dolor sit mork<br>[+]...adipiscing sed diam</p></div>
  <div class="abs why-item left" style="left:62px;top:1741px"><h3>Superior Advice</h3><p>Lorem ipsum dolor sit mork<br>[+]...adipiscing sed diam</p></div>
  <div class="abs why-item" style="left:721px;top:1530px"><h3>Expert Guidance</h3><p>Lorem ipsum dolor sit mork<br>adipiscing sed diam...[+]</p></div>
  <div class="abs why-item" style="left:825px;top:1628px"><h3>Considerable Time<br>For You</h3><p>Lorem ipsum dolor sit mork<br>adipiscing sed diam...[+]</p></div>
  <div class="abs why-item" style="left:878px;top:1727px"><h3>Deep Legal Industry<br>Relationships</h3><p>Lorem ipsum dolor sit mork<br>adipiscing sed diam...[+]</p></div>

  <div class="abs why-icon" style="left:502px;top:1579px"><svg width="36" height="36" viewBox="0 0 24 24" fill="#1e4d86"><path d="M4 3h5l1.5 4-2.5 1.5a10 10 0 0 0 5 5l1.5-2.5 4 1.5v5a2 2 0 0 1-2 2A16 16 0 0 1 2 5a2 2 0 0 1 2-2z"/><circle cx="17" cy="6" r="5"/><g fill="#fff"><circle cx="15" cy="6" r=".9"/><circle cx="17" cy="6" r=".9"/><circle cx="19" cy="6" r=".9"/></g></svg></div>
  <div class="abs why-icon" style="left:398px;top:1634px"><svg width="36" height="36" viewBox="0 0 24 24" fill="none" stroke="#1e4d86" stroke-width="2.5"><circle cx="9" cy="14" r="4" stroke-dasharray="3 1.6"/><circle cx="17" cy="7" r="3" stroke-dasharray="2.2 1.4"/></svg></div>
  <div class="abs why-icon" style="left:346px;top:1733px"><svg width="36" height="36" viewBox="0 0 24 24" fill="#1e4d86"><path d="M12 5a6 6 0 0 0-3.5 10.9V18h7v-2.1A6 6 0 0 0 12 5z"/><rect x="9" y="19" width="6" height="2"/><path d="M12 0v3M3 4l2 2M21 4l-2 2M0 11h3M24 11h-3" stroke="#1e4d86" stroke-width="1.5"/></svg></div>
  <div class="abs why-icon" style="left:628px;top:1579px"><svg width="36" height="36" viewBox="0 0 24 24" fill="#1e4d86"><circle cx="10" cy="9" r="4.5"/><path d="M2 22a8 8 0 0 1 16 0z"/><circle cx="19" cy="5" r="4" fill="none" stroke="#1e4d86" stroke-width="1.5"/><rect x="18.3" y="3" width="1.4" height="2.6" fill="#1e4d86"/></svg></div>
  <div class="abs why-icon" style="left:734px;top:1634px"><svg width="36" height="36" viewBox="0 0 24 24" fill="#1e4d86"><rect x="2" y="4" width="16" height="15" rx="1"/><g fill="#fff"><rect x="4" y="9" width="3" height="3"/><rect x="8.5" y="9" width="3" height="3"/><rect x="4" y="13.5" width="3" height="3"/></g><circle cx="18" cy="17" r="5" fill="#fff" stroke="#1e4d86" stroke-width="1.8"/><path d="M18 14.5V17h2" stroke="#1e4d86" stroke-width="1.5" fill="none"/></svg></div>
  <div class="abs why-icon" style="left:786px;top:1733px"><svg width="36" height="36" viewBox="0 0 24 24" fill="#1e4d86"><circle cx="12" cy="12" r="11" fill="none" stroke="#1e4d86" stroke-width="1.6"/><circle cx="9" cy="9" r="2.5"/><circle cx="15" cy="9" r="2.5"/><path d="M4.5 17a4.5 4.5 0 0 1 9 0zM10.5 17a4.5 4.5 0 0 1 9 0z"/></svg></div>

  <div class="abs why-hub" style="height:138px;border-bottom:none;border-radius:160px 160px 0 0">Marcus Delbridge Finance</div>
</section>

<section>
  <h2 class="abs test-title" style="font-weight:400">Clients <span>Testimonials</span></h2>
  <div class="abs rule" style="top:1952px"></div>
  <div class="abs qmark" style="left:190px;top:1972px">“</div>
  <p class="abs quote">Lorem ipsum dolor sit amet, consectetuer adipiscing elit, sed diam nonummy nibh euismod tinciduntol ut laoreet dolore magna aliquam erat volutpat. Ut wisi enim ad minim veniam, quis nostrud exercimori mornkle tation ullamcorper suscipit lobortis nisl ut aliquip ex ea commodo consequat.</p>
  <div class="abs qmark" style="left:770px;top:2040px">”</div>
  <svg class="abs chev" style="left:135px" width="24" height="46"><path d="M22 1L2 23l20 22" stroke="#999" stroke-width="1.5" fill="none"/></svg>
  <svg class="abs chev" style="left:1039px" width="24" height="46"><path d="M2 1l20 22L2 45" stroke="#999" stroke-width="1.5" fill="none"/></svg>
  <div class="abs client"><b>Renata K.</b><small>Costa Mesa, CA</small></div>
  <div class="abs dots"><span></span><span></span><span></span><span></span></div>
</section>

<section>
  <div class="abs newsletter"></div>
  <svg class="abs" style="left:164px;top:2212px" width="74" height="40" viewBox="0 0 74 40" fill="none" stroke="#fff" stroke-width="2.5">
    <rect x="24" y="4" width="44" height="30" transform="rotate(-12 46 19)"/>
    <path d="M24 9l22 14 21-19" transform="rotate(-12 46 19)"/>
    <path d="M2 18h16M6 25h12M10 32h10"/>
  </svg>
  <div class="abs nl-title">Subscribe Our Newsletter</div>
  <svg class="abs" style="left:570px;top:2222px" width="72" height="22"><path d="M2 18c20-8 40-10 64-8" stroke="#fff" stroke-width="1.5" fill="none"/><path d="M58 4l10 6-10 5" stroke="#fff" stroke-width="1.5" fill="none"/></svg>
  <div class="abs nl-input">Enter Your Email Address</div>
  <div class="abs nl-btn">SUBSCRIBE</div>
</section>

<footer>
  <div class="abs footer"></div>
  <div class="abs col-title" style="left:164px">Quick Links</div>
  <div class="abs col-title" style="left:360px">Contact Details</div>
  <div class="abs col-title" style="left:609px">Quick Inquiry</div>
  <div class="abs col-title" style="left:851px">Follow Us</div>
  <div class="abs divider" style="left:340px"></div>
  <div class="abs divider" style="left:588px"></div>
  <div class="abs divider" style="left:830px"></div>

  <ul class="abs links">
    <li>Home</li><li>Equipment Finance</li><li>Business Finance</li><li>Commercial Finance</li><li>Construction Finance</li><li>Bridging Finance</li><li>Contact Us</li>
  </ul>

  <div class="abs map" role="img" aria-label="Faint world map behind the contact details"></div>
  <div class="abs contact">
    <div class="row"><span class="dot"><svg width="10" height="10" viewBox="0 0 24 24"><path fill="#0c5297" d="M12 1a8 8 0 0 0-8 8c0 6 8 14 8 14s8-8 8-14a8 8 0 0 0-8-8zm0 11a3 3 0 1 1 0-6 3 3 0 0 1 0 6z"/></svg></span><span>Marcus Delbridge Finance<br>Street Name City Name<br>State Zipcode</span></div>
    <div class="row"><span class="dot"><svg width="10" height="10" viewBox="0 0 24 24"><path fill="#0c5297" d="M6.6 10.8a15 15 0 0 0 6.6 6.6l2.2-2.2 4.6 1.4V21A17 17 0 0 1 3 4h4.5l1.4 4.6z"/></svg></span><span>123-555-0147</span></div>
    <div class="row"><span class="dot"><svg width="10" height="10" viewBox="0 0 24 24"><rect x="3" y="9" width="18" height="12" fill="#0c5297"/><rect x="7" y="3" width="10" height="6" fill="none" stroke="#0c5297" stroke-width="2"/></svg></span><span>123-555-0147</span></div>
    <div class="row"><span class="dot"><svg width="10" height="10" viewBox="0 0 24 24"><rect x="2" y="5" width="20" height="14" fill="#0c5297"/><path d="M2 5l10 8 10-8" stroke="#fff" stroke-width="2" fill="none"/></svg></span><span>inquiry@delbridgefinance.com</span></div>
  </div>

  <div class="abs inq" style="top:2353px;height:31px">Name</div>
  <div class="abs inq" style="top:2391px;height:31px">Email</div>
  <div class="abs inq" style="top:2426px;height:64px">Message</div>
  <div class="abs submit">Submit <svg width="18" height="10" viewBox="0 0 18 10" style="margin-left:6px"><path d="M1 5h15M12 1l4 4-4 4" stroke="#fff" stroke-width="1.3" fill="none"/></svg></div>

  <div class="abs socials foot-social"><span></span><span></span><span></span><span></span></div>

  <div class="abs copyright">Copyright © 2017 Marcus Delbridge Finance. All Rights Reserved.</div>
</footer>

</body>
</html>
```